New stationary design for online film company

We need some new stationary to fit with our new logo. The stationary should be professional, clean and simple.
We need designs for a full set of business stationary.
We need - letterhead, envelopes, invoices, proposals, coverslip/note and cover page

Industry/Entity Type

Business

```html
<!DOCTYPE html>
<html lang="en">
<head>
<meta charset="utf-8">
<title>Reelhaven Stationery Set</title>
<link rel="stylesheet" href="https://fonts.googleapis.com/css2?family=Open+Sans:wght@400;600;700&display=swap">
<style>
:root{
  --navy:#0d4670;
  --teal:#6b9cb8;
  --paper:#ffffff;
  --paper-shade:#f1f2f4;
  --ink:#4a4a4a;
  --stage:#e9e6e2;
  --rule:#7fa6c0;
  --faint:#e3e6ee;
}
*{box-sizing:border-box;margin:0;padding:0}
html,body{width:1200px;height:492px;overflow:hidden}
body{background:var(--stage);font-family:"Open Sans",Arial,sans-serif;color:var(--ink);position:relative}
.sheet{position:absolute;background:linear-gradient(135deg,var(--paper) 40%,var(--paper-shade));box-shadow:0 1px 4px rgba(0,0,0,.18)}
.brand{display:flex;align-items:center;gap:5px;color:var(--teal);font-weight:600;letter-spacing:-.3px}
.brand-dot{border-radius:50%;background:var(--navy);flex:none}
.brand-dot.ring{background:none;border:3px solid var(--navy)}
.contact{font-size:5.5px;line-height:8px;color:var(--ink)}
.contact svg{width:5px;height:5px;vertical-align:-1px;margin-right:2px}

/* Letterhead option 1 */
.letterhead-one{left:8px;top:20px;width:333px;height:432px}
.letterhead-one .brand{position:absolute;left:17px;top:20px;font-size:19px}
.letterhead-one .brand-dot{width:20px;height:20px}
.letterhead-one .contact{position:absolute;left:261px;top:11px;padding-left:5px;border-left:1px solid #ccc}
.letterhead-one .contact .address{margin-top:2px;line-height:7px}
.letterhead-one .watermark{position:absolute;left:92px;top:210px;width:160px;height:160px;border-radius:50%;background:var(--faint)}

/* Letterhead option 2 */
.letterhead-two{left:374px;top:20px;width:333px;height:432px}
.letterhead-two .brand{position:absolute;left:0;right:0;top:20px;justify-content:center;font-size:19px}
.letterhead-two .brand-dot{width:20px;height:20px}
.letterhead-two .footer{position:absolute;left:0;right:0;bottom:0;height:18px;background:var(--navy);border-top:2px solid var(--rule);display:flex;justify-content:center;align-items:center;gap:5px;font-size:5.4px;color:#fff}
.letterhead-two .footer .sep{width:1px;height:7px;background:rgba(255,255,255,.5)}
.letterhead-two .footer svg{width:5px;height:5px;vertical-align:-1px;margin-right:2px}

/* Envelopes */
.envelope-back{left:822px;top:6px;width:372px;height:167px;overflow:hidden}
.envelope-back .flap{position:absolute;left:0;top:0;width:372px;height:70px}
.envelope-back .seal{position:absolute;left:171px;top:18px;width:30px;height:30px;border-radius:50%;border:4px solid #fff}
.envelope-open{left:741px;top:78px;width:373px;height:167px;overflow:hidden}
.envelope-open .flap{position:absolute;left:0;top:0;width:373px;height:68px}
.envelope-open .seal{position:absolute;left:170px;top:20px;width:32px;height:32px;border-radius:50%;border:4px solid var(--navy)}
.envelope-front{left:780px;top:152px;width:373px;height:166px}
.envelope-front .brand{position:absolute;left:10px;top:17px;font-size:17px}
.envelope-front .brand-dot{width:18px;height:18px}
.envelope-front .address{position:absolute;left:35px;top:45px;font-size:5.5px}
.envelope-front .band{position:absolute;left:0;right:0;bottom:0;height:18px;background:var(--navy);border-top:2px solid var(--rule);color:#fff;font-size:6.5px;letter-spacing:1.4px;display:flex;align-items:center;justify-content:center}

/* Business cards */
.card-front{left:771px;top:347px;width:187px;height:106px;background:var(--paper)}
.card-front .brand{position:absolute;left:34px;top:20px;font-size:16px}
.card-front .brand-dot{width:17px;height:17px}
.card-front .band{position:absolute;left:0;right:0;bottom:0;height:39px;background:var(--navy);border-top:2px solid var(--rule);color:#fff;display:flex;padding:3px 0 0}
.card-front .person{width:86px;text-align:right;padding-right:4px;border-right:1px solid rgba(255,255,255,.5);font-size:4.6px;line-height:6.4px}
.card-front .person .name{font-weight:700;font-size:6px}
.card-front .lines{padding-left:4px;font-size:4.6px;line-height:6.4px}
.card-front .lines svg{width:4.5px;height:4.5px;vertical-align:-1px;margin-right:2px}
.card-back{left:974px;top:347px;width:186px;height:106px;background:var(--navy);box-shadow:0 1px 4px rgba(0,0,0,.25)}
.card-back .seal{position:absolute;left:73px;top:21px;width:40px;height:40px;border-radius:50%;border:6px solid #fff}
.card-back .web{position:absolute;left:0;right:0;top:80px;text-align:center;color:#fff;font-size:6px;letter-spacing:1.3px}

.option-label{position:absolute;top:462px;font-size:23px;color:#6d6a66;font-weight:400;transform:translateX(-50%)}
</style>
</head>
<body>

<svg width="0" height="0" style="position:absolute">
  <symbol id="icon-phone" viewBox="0 0 10 10"><circle cx="5" cy="5" r="5" fill="currentColor"/><path d="M3 2.5l1 1-.5.8c.4.9 1 1.5 1.9 1.9l.8-.5 1 1-.7.9C4.9 7.4 2.6 5.1 2.2 3.2z" fill="#fff"/></symbol>
  <symbol id="icon-mail" viewBox="0 0 10 10"><rect x="0.5" y="2" width="9" height="6" fill="currentColor"/><path d="M1 2.5l4 3 4-3" stroke="#fff" stroke-width="1" fill="none"/></symbol>
  <symbol id="icon-web" viewBox="0 0 10 10"><circle cx="5" cy="5" r="4.5" fill="currentColor"/><circle cx="5" cy="5" r="2" fill="none" stroke="#fff" stroke-width="1"/></symbol>
</svg>

<section class="sheet letterhead-one">
  <div class="brand"><span class="brand-dot ring"></span>reelhaven</div>
  <div class="contact">
    <div><svg><use href="#icon-phone"/></svg>123-456-0789</div>
    <div><svg><use href="#icon-mail"/></svg>info@reelhaven.com</div>
    <div><svg><use href="#icon-web"/></svg>www.reelhaven.com</div>
    <div class="address">Street Name, City Name<br>State Zip Code</div>
  </div>
  <div class="watermark"></div>
</section>

<section class="sheet letterhead-two">
  <div class="brand"><span class="brand-dot ring"></span>reelhaven</div>
  <div class="footer">
    <span>Street Name, City Name, State Zip Code</span><span class="sep"></span>
    <span><svg><use href="#icon-phone"/></svg>123-456-0789</span>
    <span><svg><use href="#icon-mail"/></svg>info@reelhaven.com</span>
    <span><svg><use href="#icon-web"/></svg>www.reelhaven.com</span>
  </div>
</section>

<section class="sheet envelope-back">
  <svg class="flap" viewBox="0 0 372 70" preserveAspectRatio="none"><path d="M0 0H372V22Q370 30 340 36L186 70L32 36Q2 30 0 22Z" fill="var(--navy)"/></svg>
  <div class="seal"></div>
</section>

<section class="sheet envelope-open">
  <svg class="flap" viewBox="0 0 373 68" preserveAspectRatio="none"><path d="M1 0V12Q3 26 40 34L186 66L333 34Q370 26 372 12V0" fill="#fff" stroke="#333" stroke-width="1"/></svg>
  <div class="seal"></div>
</section>

<section class="sheet envelope-front">
  <div class="brand"><span class="brand-dot ring"></span>reelhaven</div>
  <div class="address">Street Name, City Name, State Zip Code</div>
  <div class="band">www.reelhaven.com</div>
</section>

<section class="sheet card-front">
  <div class="brand"><span class="brand-dot ring"></span>reelhaven</div>
  <div class="band">
    <div class="person"><div class="name">Your Name</div>Title<br>Street Name, City Name<br>State Zip Code</div>
    <div class="lines">
      <div><svg><use href="#icon-phone"/></svg>123-456-0789</div>
      <div><svg><use href="#icon-phone"/></svg>123-456-0789</div>
      <div><svg><use href="#icon-mail"/></svg>info@reelhaven.com</div>
      <div><svg><use href="#icon-web"/></svg>www.reelhaven.com</div>
    </div>
  </div>
</section>

<section class="sheet card-back">
  <div class="seal"></div>
  <div class="web">www.reelhaven.com</div>
</section>

<div class="option-label" style="left:166px">Option-1</div>
<div class="option-label" style="left:532px">Option-2</div>

</body>
</html>
```